Pixorama Pages with Bold Font

I want the font to be simple yet bold for Pixorama images. Its all about a simple bold readable font. I need a single pixorama page with an image and copy/text on or over the image. The words will change in the future. I'm looking for the right font. I like fiery red and yellow colors. The "One Pic" attached is a sample of what I want without the Veltro words.

```html
<!DOCTYPE html>
<html lang="en">
<head>
<meta charset="utf-8">
<title>Dana Mae Cole – Trainer for Men</title>
<link rel="stylesheet" href="https://fonts.googleapis.com/css2?family=Arimo:wght@700&display=swap">
<style>
  :root {
    --red-deep: #8a0000;
    --red-main: #c40000;
    --red-bright: #e81010;
    --lime: #c6f43c;
    --lime-light: #e6ff7a;
    --white: #ffffff;
    --shadow: rgba(40, 0, 0, 0.75);
    --skin: #c98f62;
    --skin-light: #e6c2a0;
    --hair: #e8cf96;
  }
  html, body {
    margin: 0;
    padding: 0;
    overflow: hidden;
    background: var(--red-deep);
  }
  .poster {
    position: relative;
    width: 1200px;
    height: 1200px;
    overflow: hidden;
    font-family: "Arimo", Arial, sans-serif;
    font-weight: 700;
  }
  .backdrop {
    position: absolute;
    inset: 0;
    width: 1200px;
    height: 1200px;
  }
  .model-photo {
    position: absolute;
    left: 20px;
    top: 40px;
    width: 540px;
    height: 1160px;
    border-radius: 240px 240px 0 0;
    background:
      radial-gradient(ellipse 45% 22% at 50% 14%, var(--hair) 0%, transparent 100%),
      linear-gradient(180deg, var(--skin-light) 0%, var(--skin) 55%, var(--skin-light) 100%);
    opacity: 0.9;
  }
  .brand-tag {
    position: absolute;
    right: 30px;
    top: 14px;
    margin: 0;
    font-size: 33px;
    color: var(--white);
    opacity: 0.9;
    text-shadow: 2px 2px 3px var(--shadow);
  }
  .headline {
    position: absolute;
    left: 0;
    top: 0;
    margin: 0;
    font-size: 64px;
    line-height: 1;
    color: var(--lime);
    text-shadow: 3px 3px 4px var(--shadow);
  }
  .headline span {
    position: absolute;
    white-space: nowrap;
    background: linear-gradient(180deg, var(--lime-light), var(--lime));
    -webkit-background-clip: text;
    background-clip: text;
  }
  .headline .line-1 { left: 383px; top: 112px; }
  .headline .line-2 { left: 458px; top: 208px; }
  .headline .line-3 { left: 593px; top: 274px; font-size: 66px; }
  .pitch {
    position: absolute;
    left: 0;
    top: 0;
    margin: 0;
    font-size: 40px;
    color: var(--white);
    text-shadow: 3px 3px 4px var(--shadow);
  }
  .pitch span {
    position: absolute;
    white-space: nowrap;
  }
  .social-links {
    position: absolute;
    right: 110px;
    top: 1124px;
    display: flex;
    gap: 22px;
    margin: 0;
    font-size: 24px;
    color: var(--white);
  }
</style>
</head>
<body>
<main class="poster">
  <svg class="backdrop" viewBox="0 0 1200 1200" aria-hidden="true">
    <defs>
      <radialGradient id="bg-glow" cx="0.65" cy="0.45" r="0.8">
        <stop offset="0" stop-color="var(--red-bright)"/>
        <stop offset="0.6" stop-color="var(--red-main)"/>
        <stop offset="1" stop-color="var(--red-deep)"/>
      </radialGradient>
    </defs>
    <rect width="1200" height="1200" fill="url(#bg-glow)"/>
    <path d="M0 700 C 350 500 800 380 1200 120 L1200 260 C 820 520 380 640 0 860 Z" fill="#ff3a2a" opacity="0.25"/>
    <path d="M0 1040 C 420 900 860 760 1200 520 L1200 640 C 880 860 420 1000 0 1140 Z" fill="#ff4a30" opacity="0.18"/>
    <path d="M620 0 C 760 120 980 160 1200 150 L1200 0 Z" fill="#6a0000" opacity="0.4"/>
  </svg>

  <div class="model-photo" role="img" aria-label="Photo of a blonde fitness model in a white bikini"></div>

  <p class="brand-tag">Dana Mae Cole Trainer for Men</p>

  <h1 class="headline">
    <span class="line-1">Wanna lose weight?</span>
    <span class="line-2">Wanna shrink that gut?</span>
    <span class="line-3">I can help you.</span>
  </h1>

  <p class="pitch">
    <span style="left:585px; top:462px;">The secret is to find what</span>
    <span style="left:595px; top:514px;">works for YOU !</span>
    <span style="left:600px; top:633px;">And I can give you that !</span>
    <span style="left:602px; top:750px;">The pounds will melt</span>
    <span style="left:602px; top:804px;">away, your guts will</span>
    <span style="left:597px; top:860px;">shrink, and your health</span>
    <span style="left:590px; top:921px;">will improve.</span>
  </p>

  <p class="social-links">
    <span class="social-name">Pixorama</span>
    <span class="social-name">Friendloop</span>
    <span class="social-name">Chirpline</span>
  </p>
</main>
</body>
</html>
```